BrivoTerna. Lantern of the Steady Harvest. Business card

Professional business card for BrivoTerna (Lantern of the Steady Harvest)
My rationale: Strategy-> Execution-> Results-> Value that lead to the BrivoTerna name: We put the Lantern of the Steady Harvest.
We deliver value to our customers helping them at defining a good strategy (cyan arrow). 90% of well formulated strategies fail due to poor execution so we also consider strategical execution very important (green arrow). Due to the execution we obtain the results (blue arrow). Finally, the results provide feedback to redefine strategy, and the new strategy has to be executed and new results obtained providing new feedback and on and on. It's like a wheel that finally, must create corporate value: value for shareholders, staholders, employees, providers...-

Target Market(s)

CEOs and steering comitees , invewrnent funds

Industry/Entity Type

Business Consultant

Contact Information for Business Card

Teodoro Vinsquel
CEO & Founder
teodoro.vinsquel@brivoterna-example.com
Mobile: +34 655.803.912
www.brivoterna-example.com

Colors

Designer to choose colors to be used in the design.

Requirements
Nice to have
• Nice to hace the words: Strategy, execution, results
• Nice to vave the claim: Lantern of the Steady Harvest
• The three colors should be shown:
• cyan for STRATEGY
• green for EXECUTION
• blue for RESULTS
Should not have
• Complete black background

```html
<!DOCTYPE html>
<html lang="en">
<head>
<meta charset="utf-8">
<title>BrivoTerna — Business Card</title>
<link href="https://fonts.googleapis.com/css2?family=Montserrat:wght@400;500;700&display=swap" rel="stylesheet">
<style>
  :root {
    --results-blue: #203c92;
    --execution-green: #8dc63f;
    --strategy-cyan: #29abe2;
    --card-white: #ffffff;
    --text-grey: #4a4a4a;
    --backdrop: #e9e6e2;
  }
  * { margin: 0; padding: 0; box-sizing: border-box; }
  html, body { width: 1200px; height: 909px; overflow: hidden; }
  body {
    background: var(--backdrop);
    font-family: "Montserrat", sans-serif;
    display: flex;
    flex-direction: column;
    align-items: center;
    justify-content: center;
    gap: 44px;
  }
  .card {
    position: relative;
    width: 640px;
    height: 366px;
    background: var(--card-white);
    box-shadow: 0 6px 18px rgba(0,0,0,0.18);
    overflow: hidden;
  }
  .colour-band {
    position: absolute;
    left: 0; right: 0; bottom: 0;
    height: 16px;
    display: flex;
    gap: 3px;
  }
  .band-results { background: var(--results-blue); flex: 0 0 37%; }
  .band-execution { background: var(--execution-green); flex: 0 0 33%; }
  .band-strategy { background: var(--strategy-cyan); flex: 1; }

  .brand-name {
    font-family: "Montserrat", sans-serif;
    font-weight: 700;
    color: var(--results-blue);
    letter-spacing: -0.5px;
    display: flex;
    align-items: center;
    gap: 12px;
  }
  .brand-dot {
    width: 18px; height: 18px;
    border-radius: 50%;
    background: var(--results-blue);
  }

  .card-front .brand-name {
    position: absolute;
    left: 50%; top: 44%;
    transform: translate(-50%, -50%);
    font-size: 52px;
  }

  .card-back .brand-name {
    position: absolute;
    left: 130px; top: 190px;
    transform: translateY(-50%);
    font-size: 34px;
  }
  .divider {
    position: absolute;
    left: 362px; top: 110px;
    width: 1.5px; height: 150px;
    background: var(--execution-green);
  }
  .contact-block {
    position: absolute;
    left: 380px; top: 106px;
  }
  .person-name {
    font-weight: 700;
    font-size: 19px;
    color: var(--execution-green);
  }
  .person-title {
    font-size: 12px;
    color: var(--text-grey);
    margin: 4px 0 12px;
  }
  .contact-line {
    display: flex;
    align-items: center;
    gap: 7px;
    font-size: 10.5px;
    color: var(--text-grey);
    margin-bottom: 8px;
  }
  .contact-icon { width: 11px; height: 11px; flex: none; }
</style>
</head>
<body>

<section class="card card-front">
  <div class="brand-name"><span class="brand-dot"></span>BrivoTerna</div>
  <div class="colour-band">
    <span class="band-results"></span>
    <span class="band-execution"></span>
    <span class="band-strategy"></span>
  </div>
</section>

<section class="card card-back">
  <div class="brand-name"><span class="brand-dot"></span>BrivoTerna</div>
  <div class="divider"></div>
  <div class="contact-block">
    <p class="person-name">Teodoro Vinsquel</p>
    <p class="person-title">CEO &amp; Founder</p>
    <p class="contact-line">
      <svg class="contact-icon" viewBox="0 0 12 12" aria-hidden="true">
        <rect x="3" y="0.8" width="6" height="10.4" rx="1.2" fill="none" stroke="#203c92" stroke-width="1.2"/>
        <circle cx="6" cy="9.4" r="0.7" fill="#203c92"/>
      </svg>
      +34 655.803.912
    </p>
    <p class="contact-line">
      <svg class="contact-icon" viewBox="0 0 12 12" aria-hidden="true">
        <rect x="0.5" y="2.5" width="11" height="7.5" fill="#203c92"/>
        <path d="M0.5 2.5 L6 6.8 L11.5 2.5" fill="none" stroke="#ffffff" stroke-width="1"/>
      </svg>
      teodoro.vinsquel@brivoterna-example.com
    </p>
    <p class="contact-line">
      <svg class="contact-icon" viewBox="0 0 12 12" aria-hidden="true">
        <circle cx="6" cy="6" r="5.3" fill="#203c92"/>
        <ellipse cx="6" cy="6" rx="2.3" ry="5.3" fill="none" stroke="#ffffff" stroke-width="0.8"/>
        <path d="M0.8 6 H11.2" stroke="#ffffff" stroke-width="0.8"/>
      </svg>
      www.brivoterna-example.com
    </p>
  </div>
  <div class="colour-band">
    <span class="band-results"></span>
    <span class="band-execution"></span>
    <span class="band-strategy"></span>
  </div>
</section>

</body>
</html>
```